Velmora Freightway Solutions Business cards

Would like a very unique design catchy but professional for business cards. Please use log provided.Marlon WellsCeo and Founder TransCon Logistix Solutions1-888-913-3225mwells@tlsolutionsus.comwww.tlsolutionsus.com

```html
<!DOCTYPE html>
<html lang="en">
<head>
<meta charset="utf-8">
<title>Velmora Freightway Solutions – Business Cards</title>
<link href="https://fonts.googleapis.com/css2?family=Lato:wght@400;700&family=Montserrat:wght@600&display=swap" rel="stylesheet">
<style>
  :root {
    --stage: #575757;
    --paper: #ffffff;
    --brand-red: #ec1c24;
    --brand-blue: #1a72bb;
    --ink: #3a3a3a;
    --shadow: rgba(0, 0, 0, 0.55);
  }
  * { box-sizing: border-box; margin: 0; padding: 0; }
  html, body {
    width: 1200px;
    height: 900px;
    overflow: hidden;
    background: var(--stage);
  }
  .stage {
    position: relative;
    width: 1200px;
    height: 900px;
  }
  .card {
    position: absolute;
    top: 200px;
    width: 310px;
    height: 502px;
    box-shadow: 3px 3px 5px var(--shadow);
  }
  .card--front {
    left: 253px;
    background: var(--paper);
    border-radius: 58px 0 58px 0;
  }
  .card--back {
    left: 627px;
    background: var(--brand-red);
    border-radius: 0 58px 0 58px;
  }
  .brand-name {
    position: absolute;
    left: 0;
    right: 0;
    text-align: center;
    font-family: "Montserrat", sans-serif;
    font-weight: 600;
    letter-spacing: 1px;
    text-transform: uppercase;
    line-height: 1.2;
  }
  .card--front .brand-name {
    top: 146px;
    font-size: 19px;
    color: var(--brand-blue);
  }
  .card--back .brand-name {
    top: 212px;
    font-size: 26px;
    color: var(--paper);
  }
  .holder {
    position: absolute;
    left: 33px;
    top: 342px;
  }
  .holder__name {
    font-family: "Montserrat", sans-serif;
    font-weight: 600;
    font-size: 17px;
    letter-spacing: 0.5px;
    color: var(--brand-blue);
    text-transform: uppercase;
    line-height: 20px;
  }
  .holder__surname { color: var(--brand-red); }
  .holder__title {
    font-family: "Lato", sans-serif;
    font-size: 14px;
    color: var(--ink);
    line-height: 18px;
  }
  .contact {
    position: absolute;
    left: 33px;
    top: 405px;
    list-style: none;
    font-family: "Lato", sans-serif;
    font-size: 14px;
    color: var(--ink);
  }
  .contact__item {
    display: flex;
    align-items: center;
    height: 18px;
  }
  .contact__icon {
    width: 11px;
    height: 11px;
    margin-right: 5px;
    fill: var(--brand-blue);
  }
  .back-web {
    position: absolute;
    left: 0;
    right: 0;
    top: 444px;
    text-align: center;
    font-family: "Lato", sans-serif;
    font-size: 16px;
    color: var(--paper);
  }
</style>
</head>
<body>
<main class="stage">
  <section class="card card--front" aria-label="Card front">
    <p class="brand-name">Velmora Freightway<br>Solutions</p>
    <div class="holder">
      <p class="holder__name">Dorian <span class="holder__surname">Pike</span></p>
      <p class="holder__title">CEO and Founder</p>
    </div>
    <ul class="contact">
      <li class="contact__item">
        <svg class="contact__icon" viewBox="0 0 12 12" aria-hidden="true"><path d="M1 4c0-2 2-3 5-3s5 1 5 3l-2 1-1-2H4L3 5 1 4zM3 6h6l1 5H2l1-5z"/></svg>
        1-888-470-6158
      </li>
      <li class="contact__item">
        <svg class="contact__icon" viewBox="0 0 12 12" aria-hidden="true"><path d="M0 2h12v8H0z"/><path d="M0 2l6 5 6-5" fill="none" stroke="#fff" stroke-width="1"/></svg>
        dpike@vfwayroutes.com
      </li>
      <li class="contact__item">
        <svg class="contact__icon" viewBox="0 0 12 12" aria-hidden="true"><circle cx="6" cy="6" r="5.5"/><path d="M3 4c1 0 2 1 2 2s1 1 1 3M7 2c0 1 1 2 2 2" fill="none" stroke="#fff" stroke-width="1"/></svg>
        www.vfwayroutes.com
      </li>
    </ul>
  </section>

  <section class="card card--back" aria-label="Card back">
    <p class="brand-name">Velmora<br>Freightway<br>Solutions</p>
    <p class="back-web">www.vfwayroutes.com</p>
  </section>
</main>
</body>
</html>
```